Sustainably Transforming Education

Company is education services based. early learning through adult and corporate. Focus is national government policy and program design and delivery alongside a research based and academically grounded set of approaches to planning, evaluation, and change management.I am looking for an innovative design position that aligns with the global agendas for innovation, creativity and collaboration at international and national policy levels (berulo is a name that reflects these qualities - colours need to reflect amythyst in some way). I also need a design that translates from a business card as 1 medium of interaction to a template that can work in word/powerpoint etc to support both stationery as well as a digital strategy across multiple channels (fb/twit/etc)There is no slogan/tag line for the company and their is no logo. I was looking to just leverage the name - have currently played around with various fonts (ending up with cuisine - all lowercase).

Industry/Entity Type

Adult

Contact Information for Business Card

name: berulo (all lowercase)Chairman: Andrew CrowMobile: +61 418 902 131Web: www.berulo.comemail: martin.pelly@berulo-example.com

Font styles to use
Script
Other font styles liked:
• cuisine

Colors
e34298
e667a6
33a6d7
aaaaaa

Requirements
Nice to have
• https://files.example-share.net/sh/qx7kw2hd91lzmnp/AAFr3tYbQeLp8VwZnKcDs2Hu?dl=0
• Link to the printwell templates used to begin this process....the one with the lines was about people intersecting (collaborating).....the organic shapes one more of a fluid feel of people coming together - the overall shape being largely spherical could represent a "global" feel.....anyway that is how I was thinking about these

```html
<!DOCTYPE html>
<html lang="en">
<head>
<meta charset="utf-8">
<title>berulo business card</title>
<link rel="stylesheet" href="https://fonts.googleapis.com/css2?family=Dancing+Script:wght@500;700&display=swap">
<style>
  :root {
    --bg: #ececec;
    --stripe-amethyst: #e34298;
    --stripe-orchid: #e667a6;
    --stripe-blue: #33a6d7;
    --stripe-sky: #8fcbe8;
    --stripe-lilac: #e4dde9;
    --band: #3a3a3a;
    --ink-light: #f4f4f4;
    --accent: #e667a6;
  }
  html, body {
    margin: 0;
    width: 1200px;
    height: 1152px;
    overflow: hidden;
    background: var(--bg);
  }
  .canvas {
    position: relative;
    width: 1200px;
    height: 1152px;
  }
  .card {
    position: absolute;
    left: 150px;
    width: 900px;
    height: 514px;
    display: block;
    box-shadow: 0 6px 18px rgba(0,0,0,0.18);
  }
  .card--back { top: 40px; }
  .card--front { top: 598px; }
  .stripe--amethyst { fill: var(--stripe-amethyst); }
  .stripe--orchid { fill: var(--stripe-orchid); }
  .stripe--blue { fill: var(--stripe-blue); }
  .stripe--sky { fill: var(--stripe-sky); }
  .stripe--lilac { fill: var(--stripe-lilac); }
  .band { fill: var(--band); }
  .script {
    font-family: "Dancing Script", cursive;
    fill: var(--ink-light);
  }
  .brand-name { font-size: 96px; font-weight: 500; }
  .person-name { font-size: 58px; font-weight: 500; }
  .person-role { font-size: 26px; font-weight: 500; fill: var(--accent); }
  .contact-line { font-size: 23px; font-weight: 500; }
</style>
</head>
<body>
<main class="canvas">

  <svg class="card card--back" viewBox="0 0 900 514" aria-label="berulo business card, back">
    <defs>
      <pattern id="stripes" patternUnits="userSpaceOnUse" width="20" height="190" patternTransform="rotate(30)">
        <rect class="stripe--amethyst" x="0" y="0" width="20" height="38"/>
        <rect class="stripe--orchid" x="0" y="38" width="20" height="38"/>
        <rect class="stripe--blue" x="0" y="76" width="20" height="38"/>
        <rect class="stripe--sky" x="0" y="114" width="20" height="38"/>
        <rect class="stripe--lilac" x="0" y="152" width="20" height="38"/>
      </pattern>
      <clipPath id="card-clip-back"><rect width="900" height="514"/></clipPath>
    </defs>
    <g clip-path="url(#card-clip-back)">
      <rect width="900" height="514" fill="url(#stripes)"/>
      <g transform="rotate(30 450 257)">
        <rect class="band" x="250" y="-600" width="160" height="1700"/>
        <rect class="band" x="590" y="-600" width="150" height="1700"/>
        <text class="script person-name" x="330" y="240" text-anchor="middle" transform="rotate(-90 330 240)">Martin Pelly</text>
        <text class="script person-role" x="372" y="330" text-anchor="middle" transform="rotate(-90 372 330)">Chairman</text>
        <text class="script contact-line" x="628" y="250" text-anchor="middle" transform="rotate(-90 628 250)">+61 427 315 086</text>
        <text class="script contact-line" x="666" y="250" text-anchor="middle" transform="rotate(-90 666 250)">martin.pelly@berulo-example.com</text>
        <text class="script contact-line" x="704" y="250" text-anchor="middle" transform="rotate(-90 704 250)">www.berulo-example.com</text>
      </g>
    </g>
  </svg>

  <svg class="card card--front" viewBox="0 0 900 514" aria-label="berulo business card, front">
    <defs>
      <clipPath id="card-clip-front"><rect width="900" height="514"/></clipPath>
    </defs>
    <g clip-path="url(#card-clip-front)">
      <rect width="900" height="514" fill="url(#stripes)"/>
      <g transform="rotate(30 450 257)">
        <rect class="band" x="560" y="-600" width="140" height="1700"/>
        <text class="script brand-name" x="648" y="190" text-anchor="middle" transform="rotate(-90 648 190)">berulo</text>
      </g>
    </g>
  </svg>

</main>
</body>
</html>
```